A Gallery type Web design

We are developing a Wordpress based website for a client that does design construction projects. E.g. Pools, Lobbies, Toilets, etc. The website will mainly be to showcase their past projects and the collections they have.
No programming required, we just need the designs!
A sample of what the client is looking for:
http://velmorati.it/
Pages to include:
• Home – A nice slider design to showcase selected photos
• Main Category Template
• Sub Category Template
• About us
• Contact us
Example of their Main Categories and their Sub Categories:
Collections - Granite
- Marble
- Sculpture
Projects - Private
- Public
- Commercial
- Overseas
Installation - Vanity tops
- Hall areas
- Toilets
The Main Category is to show a sample and link the user to the respective Sub Categories. The Sub Categories are to showcase all the photos they have from the category. Please leave a little space to add some text or caption for the photo.
Designs need to be mobile responsive!
I've attached their logo and some sample photos to use for mock ups. Let me know if you have any questions!

```html
<!DOCTYPE html>
<html lang="en">
<head>
<meta charset="utf-8">
<title>Terravia Stone – Home</title>
<link rel="stylesheet" href="https://fonts.googleapis.com/css2?family=Mulish:wght@300;400;500&display=swap">
<style>
  :root {
    --ink: #000000;
    --band: #a4a5a9;
    --text-light: #ffffff;
    --text-soft: #f2f2f4;
    --text-dim: #7a7a7c;
    --arrow-box: rgba(90, 90, 92, 0.55);
    --social: #4d86b4;
    --social-ring: #d8dde2;
    --hero-dark: #2a2623;
    --hero-warm: #8a7a66;
    --hero-light: #c9bfb0;
    --tile-light: #e4e4e6;
    --tile-mid: #b9babd;
    --brand-red: #d52a2a;
  }
  * { margin: 0; padding: 0; box-sizing: border-box; }
  html, body { width: 1200px; height: 816px; overflow: hidden; background: var(--band); }
  body { position: relative; font-family: "Mulish", "Helvetica Neue", Arial, sans-serif; color: var(--text-light); }
  a { color: inherit; text-decoration: none; }

  .top-bar { position: absolute; left: 0; top: 0; width: 1200px; height: 34px; background: var(--ink); font-size: 13px; font-weight: 400; }
  .language { position: absolute; left: 104px; top: 8px; color: var(--text-soft); }
  .language span { margin: 0 4px; }
  .search { position: absolute; left: 1027px; top: 10px; color: var(--text-soft); }
  .search-icon { position: absolute; left: 1086px; top: 8px; }

  .site-header { position: absolute; left: 0; top: 34px; width: 1200px; height: 107px; background: var(--band); }
  .brand { position: absolute; left: 102px; top: 34px; display: flex; align-items: center; gap: 8px; font-size: 17px; font-weight: 500; color: var(--ink); }
  .brand-mark { width: 14px; height: 14px; background: var(--brand-red); }
  .main-nav { position: absolute; top: 51px; left: 0; font-size: 15.5px; font-weight: 400; }
  .main-nav a { position: absolute; white-space: nowrap; }

  .dropdown { position: absolute; left: 617px; top: 120px; width: 118px; height: 106px; background: var(--ink); z-index: 3; font-size: 13px; }
  .dropdown::before { content: ""; position: absolute; left: 20px; top: -7px; border-left: 7px solid transparent; border-right: 7px solid transparent; border-bottom: 7px solid var(--ink); }
  .dropdown li { list-style: none; position: absolute; left: 20px; }

  .hero { position: absolute; left: 0; top: 141px; width: 1200px; height: 425px;
    background: linear-gradient(100deg, var(--hero-dark) 0%, var(--hero-warm) 35%, var(--hero-light) 62%, var(--hero-warm) 82%, var(--hero-dark) 100%); }
  .slider-arrow { position: absolute; top: 191px; width: 45px; height: 49px; background: var(--arrow-box); }
  .slider-arrow.prev { left: 24px; background: transparent; }
  .slider-arrow.next { left: 1140px; }
  .slider-arrow svg { position: absolute; left: 10px; top: 7px; }

  .social { position: absolute; left: 1159px; top: 419px; z-index: 2; }
  .social-link { display: block; width: 28px; height: 28px; border-radius: 50%; background: var(--social); border: 2px solid var(--social-ring); margin-bottom: 6px; position: relative; }
  .social-link svg { position: absolute; left: 5px; top: 5px; }

  .news-band { position: absolute; left: 0; top: 566px; width: 1200px; height: 215px; background: var(--band); }
  .news-image { position: absolute; left: 153px; top: 0; width: 217px; height: 215px;
    background: linear-gradient(135deg, var(--tile-light), var(--tile-mid) 55%, var(--tile-light)); }
  .news-toggle { position: absolute; left: 1074px; top: 14px; font-size: 14.5px; color: var(--text-soft); }
  .news-toggle-box { position: absolute; left: 1166px; top: 15px; width: 22px; height: 19px; background: #5d5e62; }
  .news-toggle-box svg { position: absolute; left: 4px; top: 5px; }
  .news-title { position: absolute; left: 390px; top: 60px; font-size: 22px; font-weight: 400; }
  .news-body { position: absolute; left: 390px; top: 97px; width: 720px; font-size: 11.5px; line-height: 17px; font-weight: 400; }
  .news-author { position: absolute; left: 393px; top: 146px; font-size: 15px; }

  .site-footer { position: absolute; left: 0; top: 781px; width: 1200px; height: 35px; background: var(--ink); font-size: 12.5px; }
  .copyright { position: absolute; left: 75px; top: 9px; }
  .footer-nav a { position: absolute; top: 10px; white-space: nowrap; font-size: 12px; }
  .page-code { position: absolute; left: 1169px; top: 10px; font-size: 12px; color: var(--text-dim); }
</style>
</head>
<body>
  <div class="top-bar">
    <div class="language">Language : EN <span>::</span>CA <span>::</span>CN <span>::</span>RU</div>
    <div class="search">Search</div>
    <svg class="search-icon" width="18" height="18" viewBox="0 0 18 18" aria-label="Search">
      <circle cx="7" cy="7" r="5.5" fill="none" stroke="#e6e6e6" stroke-width="1.4"/>
      <line x1="11" y1="11" x2="16" y2="16" stroke="#e6e6e6" stroke-width="1.6"/>
    </svg>
  </div>

  <header class="site-header">
    <div class="brand"><span class="brand-mark"></span>Terravia Stone</div>
    <nav class="main-nav">
      <a style="left:543px" href="#">Home</a>
      <a style="left:615px" href="#">Collections</a>
      <a style="left:721px" href="#">Projects</a>
      <a style="left:807px" href="#">Installations</a>
      <a style="left:922px" href="#">About us</a>
      <a style="left:1013px" href="#">Contact us</a>
    </nav>
  </header>

  <ul class="dropdown">
    <li style="top:15px">- Granite</li>
    <li style="top:43px">- Marble</li>
    <li style="top:70px">- Sculpture</li>
  </ul>

  <section class="hero" role="img" aria-label="Slider photo: warmly lit dining room with patterned chairs, lamp and framed pictures on a sideboard">
    <div class="slider-arrow prev">
      <svg width="24" height="36" viewBox="0 0 24 36"><polyline points="18,2 4,18 18,34" fill="none" stroke="#fff" stroke-width="1.3"/></svg>
    </div>
    <div class="slider-arrow next">
      <svg width="24" height="36" viewBox="0 0 24 36"><polyline points="6,2 20,18 6,34" fill="none" stroke="#fff" stroke-width="1.3"/></svg>
    </div>
  </section>

  <nav class="social" aria-label="Share and follow">
    <a class="social-link" href="#" aria-label="Share this page">
      <svg width="14" height="14" viewBox="0 0 14 14">
        <circle cx="11" cy="3" r="2" fill="#fff"/><circle cx="3" cy="7" r="2" fill="#fff"/><circle cx="11" cy="11" r="2" fill="#fff"/>
        <line x1="3" y1="7" x2="11" y2="3" stroke="#fff" stroke-width="1.2"/><line x1="3" y1="7" x2="11" y2="11" stroke="#fff" stroke-width="1.2"/>
      </svg>
    </a>
    <a class="social-link" href="#" aria-label="Send a message">
      <svg width="14" height="14" viewBox="0 0 14 14">
        <path d="M1 2 H13 V10 H6 L3 13 V10 H1 Z" fill="#fff"/>
      </svg>
    </a>
    <a class="social-link" href="#" aria-label="Copy link">
      <svg width="14" height="14" viewBox="0 0 14 14">
        <rect x="1" y="5" width="7" height="4" rx="2" fill="none" stroke="#fff" stroke-width="1.4"/>
        <rect x="6" y="5" width="7" height="4" rx="2" fill="none" stroke="#fff" stroke-width="1.4"/>
      </svg>
    </a>
  </nav>

  <section class="news-band">
    <div class="news-image" role="img" aria-label="Grey and white marble mosaic tiles"></div>
    <div class="news-toggle">Latest News</div>
    <div class="news-toggle-box">
      <svg width="14" height="9" viewBox="0 0 14 9"><polyline points="1,1 7,7 13,1" fill="none" stroke="#fff" stroke-width="1.3"/></svg>
    </div>
    <h2 class="news-title">Latest News</h2>
    <p class="news-body">Nemo enim ipsam voluptatem quia voluptas sit aspernatur aut odit aut fugit, sed quia consequuntur magni dolores eos qui ratione voluptatem sequi nesciunt.</p>
    <p class="news-author">- Dusi leo</p>
  </section>

  <footer class="site-footer">
    <div class="copyright">©2014.www.companyname.com</div>
    <nav class="footer-nav">
      <a style="left:674px" href="#">Home</a>
      <a style="left:732px" href="#">Collections</a>
      <a style="left:819px" href="#">Projects</a>
      <a style="left:888px" href="#">Installations</a>
      <a style="left:981px" href="#">About us</a>
      <a style="left:1057px" href="#">Contact us</a>
    </nav>
    <div class="page-code">M1</div>
  </footer>
</body>
</html>
```